Budget Brand Responsive Website

Flat vector style website needed for value based IT support company. looking for clean, illustration intensive based design. Current test site can be found at www.bright-mend.co.uk and holding page it www.brightmend.co.uk this will show text and services, please feel free to use placeholder text if you think we need alternative text in places. Emphasis should be on low cost support and services listed on the site, would be nice to see costs in bold images. important colors are the blue, orange and white, see holding page and attached image of an advert

It Company

```html
<!DOCTYPE html>
<html lang="en">
<head>
<meta charset="utf-8">
<title>Bright Mend – IT Support</title>
<link href="https://fonts.googleapis.com/css2?family=Raleway:wght@400;600;700;800&family=Open+Sans:wght@400;600;700&display=swap" rel="stylesheet">
<style>
:root{
  --blue:#1d5aa8;
  --blue-deep:#17407a;
  --orange:#e8772e;
  --orange-dark:#b8561a;
  --navy:#0f2340;
  --navy-deep:#0a1a30;
  --ink:#2f3a46;
  --muted:#7b8591;
  --line:#e2e6ea;
  --white:#ffffff;
}
*{margin:0;padding:0;box-sizing:border-box}
html,body{width:1200px;height:2856px;overflow:hidden}
body{font-family:'Open Sans',Arial,sans-serif;color:var(--ink);background:var(--white);position:relative}
h1,h2,h3,.nav a,.logo{font-family:'Raleway','Helvetica Neue',sans-serif}

/* header */
.site-header{height:128px;display:flex;align-items:center;justify-content:space-between;padding:0 170px}
.logo{display:flex;align-items:center;gap:12px;font-size:34px;font-weight:800;color:var(--blue);letter-spacing:1px}
.logo-mark{width:30px;height:30px;background:var(--orange)}
.nav{display:flex;gap:34px}
.nav a{font-size:14px;font-weight:700;color:var(--ink);text-decoration:none;letter-spacing:.5px}
.nav a.active{color:var(--blue)}

/* hero */
.hero{position:relative;height:472px;overflow:hidden}
.hero-photo{position:absolute;inset:0;background:linear-gradient(100deg,#0c2236 0%,#2a5470 45%,#1b3a50 70%,#0e2131 100%)}
.hero-content{position:relative;text-align:center;padding-top:152px;color:var(--white)}
.hero h1{font-size:44px;font-weight:800;letter-spacing:1.5px}
.hero-sub{font-family:'Raleway',sans-serif;font-size:24px;font-weight:700;letter-spacing:2px;margin-top:6px}
.btn{display:inline-block;font-size:13px;font-weight:600;color:var(--white);background:var(--orange);text-decoration:none}
.hero .btn{margin-top:28px;padding:12px 26px;border-radius:3px}
.hero-dots{position:absolute;left:0;right:0;bottom:26px;display:flex;justify-content:center;gap:10px}
.hero-dots span{width:12px;height:12px;border-radius:50%;background:rgba(255,255,255,.5)}
.hero-dots span.on{background:var(--white)}

/* services */
.services{padding:60px 170px 40px;display:grid;grid-template-columns:repeat(3,1fr);gap:50px 40px}
.service{text-align:center}
.service-photo{height:128px;border-radius:2px}
.service h3{font-size:22px;font-weight:600;margin:14px 0 8px;color:var(--ink)}
.service p{font-size:12px;line-height:1.55;color:var(--muted);padding:0 18px}
.btn-outline{display:inline-block;margin-top:12px;padding:6px 16px;border:1px solid var(--orange);color:var(--orange);font-size:12px;font-weight:600;border-radius:2px;text-decoration:none}

/* prices */
.prices{margin-top:20px;height:372px;background:linear-gradient(180deg,#f08a3c 0%,var(--orange) 60%,#d8692a 100%);position:relative;padding:0 170px}
.prices-title{display:block;width:420px;margin:0 auto;background:var(--orange-dark);color:var(--white);text-align:center;font-size:22px;font-weight:700;padding:12px 0}
.price-cards{display:grid;grid-template-columns:repeat(4,1fr);gap:26px;margin-top:22px}
.price-card{background:var(--white);text-align:center;padding-bottom:16px}
.price-photo{height:108px}
.price-card h3{font-size:16px;font-weight:800;color:var(--orange);margin-top:10px}
.price-card .tag{font-size:10px;color:var(--muted);margin:2px 0 8px}
.price-row{display:flex;justify-content:space-between;font-size:11px;padding:1px 34px}
.price-row b{color:var(--ink);font-weight:700}
.btn-small{display:inline-block;margin-top:10px;padding:5px 14px;border:1px solid var(--ink);font-size:10px;font-weight:700;color:var(--ink);text-decoration:none}

/* about */
.about{height:400px;background:linear-gradient(120deg,var(--blue-deep) 0%,var(--blue) 55%,#2f74c4 100%);color:var(--white);text-align:center;padding:54px 250px 0}
.section-title{font-size:34px;font-weight:700;letter-spacing:1px}
.section-title::after{content:"";display:block;width:560px;height:1px;background:rgba(255,255,255,.5);margin:10px auto 26px}
.about p{font-size:12px;line-height:1.7;margin-bottom:14px}

/* technical support */
.tech{height:368px;padding:56px 170px 0}
.tech .section-title{text-align:center;color:var(--ink)}
.tech .section-title::after{background:var(--line)}
.tech-body{display:flex;gap:60px}
.tech-text{flex:1}
.tech-text p{font-size:12px;line-height:1.65;color:var(--muted);margin-bottom:14px}
.tech-photo{width:330px;height:190px;background:linear-gradient(135deg,#0d1b2c,#23486b 60%,#0f2236)}

/* contact */
.contact{height:360px;background:var(--navy);color:var(--white);padding:48px 170px 0}
.contact .section-title{text-align:center}
.contact .section-title::after{background:rgba(255,255,255,.3)}
.contact-body{display:flex;justify-content:space-between}
.offices{display:grid;grid-template-columns:200px 200px;gap:26px 40px;font-size:11px;line-height:1.6;color:#c7d1de}
.offices h4{font-size:12px;font-weight:700;color:var(--white)}
.contact-form{width:330px;display:flex;flex-direction:column;gap:8px}
.field{height:26px;background:var(--white);border-radius:2px;font-size:11px;color:var(--muted);padding:5px 10px}
.field.message{height:62px}
.submit{align-self:flex-start;background:var(--blue);color:var(--white);font-size:11px;font-weight:700;padding:7px 20px;border-radius:2px}

/* footer */
.site-footer{height:56px;background:var(--navy-deep);display:flex;align-items:center;justify-content:space-between;padding:0 170px;font-size:10px;color:#8d9aab}
.social{display:flex;gap:10px}
.social span{width:14px;height:14px;border-radius:50%;background:#c7d1de}
</style>
</head>
<body>

<header class="site-header">
  <div class="logo"><span class="logo-mark"></span>BRIGHT MEND</div>
  <nav class="nav">
    <a href="#" class="active">HOME</a><a href="#">SUPPORT</a><a href="#">SERVICES</a><a href="#">ABOUT</a><a href="#">CONTACT</a>
  </nav>
</header>

<section class="hero">
  <div class="hero-photo" role="img" aria-label="Technician working on network cabling in a server room"></div>
  <div class="hero-content">
    <h1>HOSTING &amp; INTERNET SUPPORT</h1>
    <p class="hero-sub">PELLENTESQUE FAUCIBUS UT ACCUMSAN</p>
    <a href="#" class="btn">Learn More</a>
  </div>
  <div class="hero-dots"><span></span><span class="on"></span><span></span><span></span></div>
</section>

<section class="services">
  <div class="service">
    <div class="service-photo" role="img" aria-label="Support agent wearing a headset" style="background:linear-gradient(135deg,#dfe7ef,#9fb6cc)"></div>
    <h3>Support</h3>
    <p>Lorem ipsum dolor sit amet, consectetur adipiscing elit, sed do eiusmod tempor incididunt ut labore et dolore.</p>
    <a href="#" class="btn-outline">Read More</a>
  </div>
  <div class="service">
    <div class="service-photo" role="img" aria-label="Office worker on a phone call" style="background:linear-gradient(135deg,#e9eef3,#b7c6d4)"></div>
    <h3>Voice</h3>
    <p>Lorem ipsum dolor sit amet, consectetur adipiscing elit, sed do eiusmod tempor incididunt ut labore et dolore.</p>
    <a href="#" class="btn-outline">Read More</a>
  </div>
  <div class="service">
    <div class="service-photo" role="img" aria-label="Glowing network connection graphic" style="background:linear-gradient(135deg,#0b2a5a,#1f63b8)"></div>
    <h3>Internet</h3>
    <p>Lorem ipsum dolor sit amet, consectetur adipiscing elit, sed do eiusmod tempor incididunt ut labore et dolore.</p>
    <a href="#" class="btn-outline">Read More</a>
  </div>
  <div class="service">
    <div class="service-photo" role="img" aria-label="Digital security padlock graphic" style="background:linear-gradient(135deg,#1a5fa0,#4fa0d8)"></div>
    <h3>Security</h3>
    <p>Lorem ipsum dolor sit amet, consectetur adipiscing elit, sed do eiusmod tempor incididunt ut labore et dolore.</p>
    <a href="#" class="btn-outline">Read More</a>
  </div>
  <div class="service">
    <div class="service-photo" role="img" aria-label="Rows of hosting servers" style="background:linear-gradient(135deg,#0a2238,#2d6a92)"></div>
    <h3>Hosting</h3>
    <p>Lorem ipsum dolor sit amet, consectetur adipiscing elit, sed do eiusmod tempor incididunt ut labore et dolore.</p>
    <a href="#" class="btn-outline">Read More</a>
  </div>
  <div class="service">
    <div class="service-photo" role="img" aria-label="Cloud computing concept graphic" style="background:linear-gradient(135deg,#2a77c4,#8cc4ee)"></div>
    <h3>Cloud</h3>
    <p>Lorem ipsum dolor sit amet, consectetur adipiscing elit, sed do eiusmod tempor incididunt ut labore et dolore.</p>
    <a href="#" class="btn-outline">Read More</a>
  </div>
</section>

<section class="prices">
  <h2 class="prices-title">Most Popular Service Prices</h2>
  <div class="price-cards">
    <div class="price-card">
      <div class="price-photo" role="img" aria-label="Support desk worker with headset" style="background:linear-gradient(135deg,#dde5ee,#a7bacc)"></div>
      <h3>SUPPORT</h3><p class="tag">Unlimited remote help desk</p>
      <div class="price-row"><span>Per user</span><b>£8.50</b></div>
      <div class="price-row"><span>Per site</span><b>£45.00</b></div>
      <div class="price-row"><span>Per year</span><b>£95.00</b></div>
      <a href="#" class="btn-small">VIEW MORE</a>
    </div>
    <div class="price-card">
      <div class="price-photo" role="img" aria-label="Smiling caller using a phone" style="background:linear-gradient(135deg,#efe9e2,#c9bdb0)"></div>
      <h3>VOICE</h3><p class="tag">Business phone lines and calls</p>
      <div class="price-row"><span>Per line</span><b>£6.00</b></div>
      <div class="price-row"><span>Per handset</span><b>£12.00</b></div>
      <div class="price-row"><span>Per year</span><b>£65.00</b></div>
      <a href="#" class="btn-small">VIEW MORE</a>
    </div>
    <div class="price-card">
      <div class="price-photo" role="img" aria-label="Server hardware in a data centre" style="background:linear-gradient(135deg,#111c28,#3c5a74)"></div>
      <h3>HOSTING</h3><p class="tag">Secure web and email hosting</p>
      <div class="price-row"><span>Starter</span><b>£4.99</b></div>
      <div class="price-row"><span>Business</span><b>£14.99</b></div>
      <div class="price-row"><span>Per year</span><b>£49.00</b></div>
      <a href="#" class="btn-small">VIEW MORE</a>
    </div>
    <div class="price-card">
      <div class="price-photo" role="img" aria-label="Business person with cloud icons" style="background:linear-gradient(135deg,#e6eef6,#a9c6e2)"></div>
      <h3>CLOUD</h3><p class="tag">Backup and cloud storage</p>
      <div class="price-row"><span>50 GB</span><b>£5.00</b></div>
      <div class="price-row"><span>500 GB</span><b>£20.00</b></div>
      <div class="price-row"><span>Per year</span><b>£55.00</b></div>
      <a href="#" class="btn-small">VIEW MORE</a>
    </div>
  </div>
</section>

<section class="about">
  <h2 class="section-title">ABOUT OUR COMPANY</h2>
  <p>Bright Mend provides low cost IT support to small businesses and home offices. Our friendly engineers solve everyday problems quickly, so you can get back to work without worrying about your computers, phones or network.</p>
  <p>We keep prices simple and fair, with clear monthly plans and no hidden fees. Every plan includes remote help, regular checks and honest advice on the equipment and services that suit your budget and your business.</p>
  <p>From hosting and email to cloud backup, security and voice lines, we look after the technology behind your business. Talk to our team today and find out how much you could save with a plan built around you.</p>
</section>

<section class="tech">
  <h2 class="section-title">TECHNICAL SUPPORT</h2>
  <div class="tech-body">
    <div class="tech-text">
      <p>Our highly skilled and certified engineers are on hand to support your business with remote and on site visits, keeping your systems running smoothly every day of the week.</p>
      <p>We monitor your servers, laptops and network around the clock and fix issues before they turn into downtime, so your staff stay productive.</p>
      <p>Planned maintenance and updates are scheduled at quiet times, and our help desk is always ready to answer questions in plain, friendly language.</p>
    </div>
    <div class="tech-photo" role="img" aria-label="Engineer working inside a server room"></div>
  </div>
</section>

<section class="contact">
  <h2 class="section-title">CONTACT US</h2>
  <div class="contact-body">
    <div class="offices">
      <div><h4>Riverside Office</h4>12 Mill Lane<br>Riverside Park<br>t: +44 (0)1700 555 010</div>
      <div><h4>Support</h4>support@brightmend.co.uk<br>t: +44 (0)1700 555 011</div>
      <div><h4>Hillcrest Office</h4>4 Station Road<br>Hillcrest<br>e: info@brightmend.co.uk</div>
      <div><h4>Sales</h4>sales@brightmend.co.uk<br>t: +44 (0)1700 555 012</div>
    </div>
    <div class="contact-form">
      <div class="field">Name</div>
      <div class="field">Email</div>
      <div class="field message">Message</div>
      <div class="submit">SUBMIT</div>
    </div>
  </div>
</section>

<footer class="site-footer">
  <span>© 2015 Bright Mend. All rights reserved. Terms of Use</span>
  <div class="social"><span></span><span></span><span></span><span></span></div>
</footer>

</body>
</html>
```